Design NEW business card

We would like a business card using the colour deep red wine or dark navy blue textured background (patterned or not, open to suggestions) with a high gloss debossed rose gold/copper RM Roland Mercer Jewellery business name (Provided). I have included images for your review we would like to keep our currently logo and business name on the front but you can change the layout and positioning. For the back of the card we are open to all suggestions/variations.
Business
Use our current RM Roland Mercer Jewellery logo (Provided image)

```html
<!DOCTYPE html>
<html lang="en">
<head>
<meta charset="utf-8">
<title>Roland Mercer Jewellery – Business Card</title>
<link rel="stylesheet" href="https://fonts.googleapis.com/css2?family=Open+Sans:wght@400&display=swap">
<style>
  :root {
    --backdrop: #2b2b2d;
    --wine: #5c1e27;
    --wine-deep: #4f1820;
    --rose-gold: #c9926e;
    --ink-light: #f6f0ee;
  }
  * { margin: 0; padding: 0; box-sizing: border-box; }
  html, body { width: 1200px; height: 900px; overflow: hidden; }
  body {
    background: var(--backdrop);
    font-family: "Open Sans", Arial, sans-serif;
    position: relative;
  }
  .card {
    position: absolute;
    top: 300px;
    width: 525px;
    height: 300px;
    border-radius: 22px;
    background: radial-gradient(circle at 40% 40%, var(--wine), var(--wine-deep));
  }
  .card--front { left: 50px; }
  .card--back { left: 625px; }

  .brand {
    position: absolute;
    display: flex;
    align-items: center;
    gap: 12px;
    color: var(--rose-gold);
    font-weight: 400;
    letter-spacing: 3px;
    text-transform: uppercase;
  }
  .brand__dot {
    width: 34px; height: 34px;
    border-radius: 50%;
    background: var(--rose-gold);
    flex: none;
  }
  .brand__name { font-size: 15px; line-height: 1.3; }
  .card--front .brand { left: 40px; top: 168px; }
  .card--back .brand { left: 50%; top: 50%; transform: translate(-50%, -50%); }
  .card--back .brand__name { font-size: 19px; }

  .contact {
    position: absolute;
    left: 300px;
    top: 60px;
    color: var(--ink-light);
    font-size: 13px;
    line-height: 1.45;
  }
  .contact__name { font-size: 19px; line-height: 1.2; }
  .contact__role { margin-bottom: 14px; }
  .contact__address { margin-bottom: 12px; }
  .contact__line { display: flex; align-items: center; gap: 9px; }
  .contact__line svg { width: 12px; height: 12px; fill: var(--ink-light); flex: none; }
</style>
</head>
<body>
  <section class="card card--front">
    <div class="brand">
      <span class="brand__dot"></span>
      <span class="brand__name">Roland Mercer<br>Jewellery</span>
    </div>
    <div class="contact">
      <p class="contact__name">Daniel Hart</p>
      <p class="contact__role">Managing Director</p>
      <p class="contact__address">48 Carver Lane, Suite 2<br>Eastfield, 204816.</p>
      <p class="contact__line">
        <svg viewBox="0 0 24 24"><path d="M6.6 10.8a15 15 0 0 0 6.6 6.6l2.2-2.2c.3-.3.7-.4 1-.2 1.1.4 2.3.6 3.6.6.6 0 1 .4 1 1V20c0 .6-.4 1-1 1A17 17 0 0 1 3 4c0-.6.4-1 1-1h3.5c.6 0 1 .4 1 1 0 1.3.2 2.5.6 3.6.1.3 0 .7-.2 1z"/></svg>
        044-318 902 457
      </p>
      <p class="contact__line">
        <svg viewBox="0 0 24 24"><path d="M2 5h20v14H2z M2 5l10 8 10-8" stroke="#5c1e27" stroke-width="1.5"/></svg>
        hello@rmjewels.com
      </p>
      <p class="contact__line">
        <svg viewBox="0 0 24 24"><path d="M10 14a4 4 0 0 0 5.7 0l4-4a4 4 0 0 0-5.7-5.7l-1.5 1.5 1.4 1.4 1.5-1.5a2 2 0 0 1 2.9 2.9l-4 4a2 2 0 0 1-2.9 0zM14 10a4 4 0 0 0-5.7 0l-4 4A4 4 0 0 0 10 19.7l1.5-1.5-1.4-1.4-1.5 1.5a2 2 0 0 1-2.9-2.9l4-4a2 2 0 0 1 2.9 0z"/></svg>
        www.rmjewels.com
      </p>
    </div>
  </section>

  <section class="card card--back">
    <div class="brand">
      <span class="brand__dot"></span>
      <span class="brand__name">Roland Mercer<br>Jewellery</span>
    </div>
  </section>
</body>
</html>
```